Our business name is Quillbrook Pty Ltd and we already have a logo. We would like the same colours that appear in our logo on our marketing material. I have attached our logo for colour consistency. We need a brochure designed that promotes our aerial photography and aerial imaging services. We'd like to use the brochure for electronic marketing purposes in an effort to attract a new client base. We are a new start up business so funds are fairly scarce. We use sophisticated UAV (unmanned aerial vehicle) or RPA - remotely piloted aircraft technology) that captures beautiful video and still images.
Our services are suitable for many types of industries and applications. We have identified at least 10 market sectors ranging, infrastructure inspections such as: gas pipelines, chemical and petrol storage facilities, pipeline and power line inspections, Archeological and geological surveys, vegetation mapping, wildlife surveys, agriculture and horticulture surveys, high end real estate, sport and event marketing. Our plan is to create a series of brochures (1) for each industry to help us market our business.

Our first brochure will focus on environmental management and compliance. We will target other industries down the track. These industries would see our service as helping them meet their compliance and auditing requirements.
We have a brochure that we put together containing words and some (very boring) format. As this will be one of a series of brochures, we'd like to colour code the industries for easy identification. (perhaps a green tab) in the corner to distinguish between our brochures. We have attached our boring brochure as a starting point. If we like the design there will be more work to follow. We want to be able to standardise the format for the other industries we will target. We anticipate needing another 6-8 brochures over the course of the next 2 months.

I have received questions regarding brochure size.  Apologies, I should have indicated in my posting previously.  The brochure is A3 landscape size so it can be folded in half to make 4 A4 pages.  We need to keep printing costs down so the content needs to be  within 4 pages.  I'm about to make some minor changes to the content to try to reduce the amount of text cause I can see this may be a problem.  Look forward to receiving your design. Thanking you in advance for your great work!

Re: Brochure Quillbrook Environmental Compliance and Monitoring Services

I have reduced the amount of text contained in the original version of the brochure making it more succinct and less wordy.  Could you use the least amount of space because we want to be able to use this brochure as both electric marketing and print based.  I have also included additional photos which will give you more to work with.  Thank you for your work in advance!  Regards Marta 

PLEASE NOTE - TEXT HAS BEEN UPDATED (REDUCED TEXT IN BROCHURE). COULD YOU REFER TO VERSION 2 OF QUILLBROOK ENVIRONMENTAL COMPLIANCE AND MONITORING SERVICES BROCHURE UPDATED FRIDAY 17TH.

Thanks Marta 

Hi talented designers working on the Quillbrook Brochure for Environmental Compliance and Monitoring.  I have been asked to upload the EPS version of Quillbrook Logo.  I have just done so.

Regards
Marta 

Hi all, to assist you with the design concept. I feel I need to clarity a number of points.  We are a new technology driven business.  No one else is conducting environmental surveys using this type of sophisticated equipment. We are in the business of providing clients with visual data (aerial images). Could you include grab lines in the brochure that draws attention to this. We us state of the art technology to produce high quality images efficiently, safely and economically. 

Thank you
Marta

Reason: We need additional time to receive and review designs.

Reason: Need additional time to communicate with designers and to review changes. Thank you Marta

I have extended the project date a few days. I have been incredibly impressed by the quality of your work and thank you all for your efforts.  I am waiting on a few revisions by a number of designers and look forward to receiving these changes.  We are close to completion.  Thanking you all again. Marta 

We are targeting a wide range of industry sectors. Specifically, looking at targeting large engineering type consultancies, corporations, government agencies, auditing bodies. Typically, targeting the professional sector who use data to confirm, monitor and make better decisions.

We want the brochure design to be contemporary and modern which reflects what our business does. We use state of the art unmanned aerial technology to capture brilliant visual images and video. So we want our brochure to reflect that we're leaders in the field offering something different - cutting edge approach. I have additional photos that show vegetation mapping, wildlife surveys, agriculture and horticulture applications. Our services would benefit any business that uses visual data to help them make better, more informed decisions.

Business

Serif
Sans Serif

• We would like you to include photo of the UAV equipment/technology shots. This is new technology so we must also educate our clients on what our technology is capable of doing. We are offering a service that is very different so we want to be able to convey the true benefits of our services such as safety, efficiency, cost saving, reliability. We would like to convey these key themes. Credible data enables businesses to make better, faster decisions.
• We are essentially providing visual data in the form of high definition photos and videos. For this particular sector, data could be used for compliance or auditing purposes, planning, measuring, monitoring, evaluating, assessing, marketing. Could you please include these words in the brochure as they capture our service provision. Please note the red photo is infrared images.

```html
<!DOCTYPE html>
<html lang="en">
<head>
<meta charset="utf-8">
<title>Quillbrook – Aerial Photography and Aerial Imaging Services</title>
<link rel="stylesheet" href="https://fonts.googleapis.com/css2?family=Bitter:wght@400&family=Source+Sans+3:wght@400;600&display=swap">
<style>
  :root {
    --brand-blue: #29a9e1;
    --brand-green: #7cc242;
    --ink-grey: #6b6b6b;
    --tab-grey: #d6d6d6;
    --paper: #ffffff;
    --paper-shade: #f1f2f3;
    --backdrop: #e6e7e8;
  }
  * { box-sizing: border-box; margin: 0; padding: 0; }
  html, body { width: 1200px; height: 845px; overflow: hidden; }
  body {
    background: var(--backdrop);
    font-family: "Source Sans 3", "Helvetica Neue", Arial, sans-serif;
    position: relative;
  }
  .spread { position: absolute; left: 52px; top: 35px; width: 1098px; height: 775px; }
  .page {
    position: absolute; top: 0; width: 548px; height: 775px; overflow: hidden;
    background: linear-gradient(160deg, var(--paper) 40%, var(--paper-shade) 100%);
  }
  .page--back { left: 0; }
  .page--front { left: 550px; }

  .photo { position: absolute; left: 22px; top: 23px; width: 502px; height: 330px; }
  .photo--farmland {
    background: linear-gradient(180deg, #c9d6dc 0%, #9fb1a2 10%, #6f8a5c 24%, #aebfc3 30%, #7d9462 42%, #b9a98a 52%, #8c9a72 60%, #3f7a3a 68%, #3c7838 100%);
  }
  .page--front .photo { top: 22px; }
  .photo--parkland {
    background: linear-gradient(150deg, #4b6a3a 0%, #6fae3e 30%, #8fcb48 55%, #6aa83c 80%, #3f6a2c 100%);
  }

  .brand-name {
    position: absolute; left: 22px; top: 380px;
    font-family: "Source Sans 3", Arial, sans-serif; font-weight: 600;
    font-size: 38px; letter-spacing: -0.5px; line-height: 1; color: var(--brand-blue);
  }

  .tab { position: absolute; }

  .contact-heading {
    position: absolute; left: 22px; top: 449px;
    display: flex; align-items: center; gap: 22px;
  }
  .contact-heading h2 {
    font-weight: 400; font-size: 22px; color: var(--brand-blue);
  }
  .contact-list { position: absolute; left: 85px; top: 490px; }
  .contact-item { margin-bottom: 14px; }
  .contact-item dt { font-size: 10.5px; color: var(--brand-green); line-height: 14px; }
  .contact-item dd { font-size: 10.5px; color: var(--ink-grey); line-height: 14.5px; }
  .contact-item dd.spaced { letter-spacing: 1.6px; }
  .contact-item dd.wide { letter-spacing: 2.2px; }

  .headline {
    position: absolute; left: 49px; top: 516px;
    font-family: "Bitter", Georgia, serif; font-weight: 400;
    font-size: 37px; line-height: 40px; color: var(--brand-blue);
    white-space: nowrap;
  }
  .headline span { display: block; }
  .headline span + span { padding-left: 59px; }

  .colour-band { position: absolute; left: 0; bottom: 0; width: 100%; height: 11px; display: flex; }
  .colour-band .blue { background: var(--brand-blue); }
  .colour-band .green { background: var(--brand-green); }
</style>
</head>
<body>
<div class="spread">

  <section class="page page--back" aria-label="Back cover">
    <div class="photo photo--farmland" role="img" aria-label="Aerial photograph of green crop fields beside a road with wetlands and ponds beyond"></div>

    <div class="brand-name">QUILLBROOK</div>

    <svg class="tab" style="left:493px;top:369px" width="55" height="100" viewBox="0 0 55 100" aria-hidden="true">
      <polygon points="55,0 55,100 0,50" fill="var(--tab-grey)"/>
    </svg>
    <svg class="tab" style="left:0;top:653px" width="52" height="100" viewBox="0 0 52 100" aria-hidden="true">
      <polygon points="0,0 52,48 0,100" fill="var(--tab-grey)"/>
    </svg>

    <div class="contact-heading">
      <svg width="40" height="40" viewBox="0 0 40 40" aria-hidden="true">
        <circle cx="20" cy="20" r="18.5" fill="none" stroke="var(--brand-green)" stroke-width="2"/>
        <path d="M11 20h17M21 13l7 7-7 7" fill="none" stroke="var(--brand-green)" stroke-width="2.6" stroke-linecap="round" stroke-linejoin="round"/>
      </svg>
      <h2>Contact Us</h2>
    </div>

    <dl class="contact-list">
      <div class="contact-item">
        <dt>Address:</dt>
        <dd>Quillbrook</dd>
        <dd>27 Harrow Lane, Suite 4</dd>
        <dd>Ferndale Park, 40512</dd>
      </div>
      <div class="contact-item">
        <dt>Phone:</dt>
        <dd class="spaced">(555) 318-2046</dd>
      </div>
      <div class="contact-item">
        <dt>Fax:</dt>
        <dd class="spaced">(555) 318-2047</dd>
      </div>
      <div class="contact-item">
        <dt>Website:</dt>
        <dd class="wide">www.quillbrook.com.au</dd>
      </div>
    </dl>

    <div class="colour-band"><div class="blue" style="width:320px"></div><div class="green" style="flex:1"></div></div>
  </section>

  <section class="page page--front" aria-label="Front cover">
    <div class="photo photo--parkland" role="img" aria-label="Top-down aerial photograph of parkland with trees, lawn and winding paths"></div>

    <div class="brand-name">QUILLBROOK</div>

    <svg class="tab" style="left:493px;top:369px" width="55" height="100" viewBox="0 0 55 100" aria-hidden="true">
      <polygon points="55,0 55,100 0,50" fill="var(--tab-grey)"/>
    </svg>
    <svg class="tab" style="left:6px;top:657px" width="46" height="92" viewBox="0 0 46 92" aria-hidden="true">
      <polygon points="0,0 46,46 0,92" fill="var(--tab-grey)"/>
    </svg>

    <h1 class="headline">
      <span>Aerial Photography and</span>
      <span>Aerial Imaging Services</span>
    </h1>

    <div class="colour-band"><div class="green" style="width:320px"></div><div class="blue" style="flex:1"></div></div>
  </section>

</div>
</body>
</html>
```